Business Card Design

We need a business card designed for our new company. Prefer a black card with white logo & writing.

Contact Information for Business Card

Ted Galloway, address: 7-4812 Fernhollow Road, Abbotsford, BC, V3K 8R2, Office Phone: 604-712-3390, Cell: 604-947-2164, Email: ted@resinworkshub.ca

Colors

Designer to choose only greyscale colors for use in the design.

```html
<!DOCTYPE html>
<html lang="en">
<head>
<meta charset="utf-8">
<title>Resin Works Hub – Business Card</title>
<link href="https://fonts.googleapis.com/css2?family=Poppins:wght@400;500;700&display=swap" rel="stylesheet">
<style>
  :root {
    --page: #cfcfcf;
    --card-dark: #0b0b0b;
    --card-light: #ffffff;
    --ink-light: #ffffff;
    --ink-dark: #1c1c1c;
  }
  * { margin: 0; padding: 0; box-sizing: border-box; }
  html, body { width: 900px; height: 1200px; overflow: hidden; }
  body {
    background: var(--page);
    font-family: "Poppins", sans-serif;
    position: relative;
  }
  .card {
    position: absolute;
    left: 134px;
    width: 632px;
    height: 362px;
  }
  .card--front { top: 212px; background: var(--card-dark); }
  .card--back  { top: 628px; background: var(--card-light); color: var(--ink-dark); }

  .brand-name {
    position: absolute;
    font-weight: 700;
    white-space: nowrap;
    letter-spacing: 0.5px;
  }
  .card--front .brand-name {
    color: var(--ink-light);
    font-size: 42px;
    left: 50%; top: 50%;
    transform: translate(-50%, -50%);
  }
  .card--back .brand-name {
    color: var(--ink-dark);
    font-size: 25px;
    left: 172px; top: 188px;
    transform: translate(-50%, -50%);
  }

  .divider {
    position: absolute;
    left: 340px; top: 88px;
    width: 2px; height: 182px;
    background: var(--ink-dark);
  }
  .contact {
    position: absolute;
    left: 373px; top: 78px;
  }
  .contact__name {
    font-size: 22px; font-weight: 700;
    letter-spacing: 0.5px; line-height: 1.2;
  }
  .contact__role {
    font-size: 13.5px; font-weight: 400;
    margin-top: 3px;
  }
  .contact__address {
    font-size: 13.5px; line-height: 1.45;
    margin-top: 10px;
  }
  .contact__list {
    list-style: none;
    margin-top: 11px;
  }
  .contact__item {
    display: flex; align-items: center;
    font-size: 14px; line-height: 22.5px;
    letter-spacing: 1px;
  }
  .contact__item svg {
    width: 12px; height: 12px;
    margin-right: 8px; flex: none;
  }
</style>
</head>
<body>
  <section class="card card--front">
    <span class="brand-name">RESIN WORKS HUB</span>
  </section>

  <section class="card card--back">
    <span class="brand-name">RESIN WORKS HUB</span>
    <div class="divider"></div>
    <div class="contact">
      <p class="contact__name">TED GALLOWAY</p>
      <p class="contact__role">Manager</p>
      <p class="contact__address">7-4812 Fernhollow Road,<br>Abbotsford, BC, V3K 8R2</p>
      <ul class="contact__list">
        <li class="contact__item">
          <svg viewBox="0 0 24 24" aria-hidden="true"><path fill="#1c1c1c" d="M6.6 10.8a15.1 15.1 0 0 0 6.6 6.6l2.2-2.2a1 1 0 0 1 1-.25 11.4 11.4 0 0 0 3.6.57 1 1 0 0 1 1 1V20a1 1 0 0 1-1 1A17 17 0 0 1 3 4a1 1 0 0 1 1-1h3.5a1 1 0 0 1 1 1c0 1.25.2 2.45.57 3.57a1 1 0 0 1-.25 1z"/></svg>
          604-712-3390
        </li>
        <li class="contact__item">
          <svg viewBox="0 0 24 24" aria-hidden="true"><rect x="6" y="1.5" width="12" height="21" rx="2" fill="#1c1c1c"/><rect x="8" y="4" width="8" height="13" fill="#fff"/><circle cx="12" cy="19.5" r="1.1" fill="#fff"/></svg>
          604-947-2164
        </li>
        <li class="contact__item">
          <svg viewBox="0 0 24 24" aria-hidden="true"><rect x="2" y="5" width="20" height="14" rx="1.5" fill="#1c1c1c"/><path d="M3 6.5l9 6.5 9-6.5" fill="none" stroke="#fff" stroke-width="1.6"/></svg>
          ted@resinworkshub.ca
        </li>
        <li class="contact__item">
          <svg viewBox="0 0 24 24" aria-hidden="true"><circle cx="12" cy="12" r="10" fill="#1c1c1c"/><g fill="none" stroke="#fff" stroke-width="1.4"><ellipse cx="12" cy="12" rx="4" ry="9.5"/><path d="M2.5 12h19M4 7h16M4 17h16"/></g></svg>
          www.resinworkshub.ca
        </li>
      </ul>
    </div>
  </section>
</body>
</html>
```